Homeowners Insurance Provider Website

We are selling homeowners insurance policy / tenants Policy/Flood Insurance in USA in few states and planning expand nationally.

Our target audience are two folds: Customers (Buy policies) and Insurance Agents who wants to work with us to sell our policies to customers. But website should focus 80% on customers and 20% on agents. So, more customer focused user experience. Please note that there is no direct buy option for customers. They always go through insurance agents.

Customer focused, educational that makes buyer journey easy. We don’t want to come off as trying sell something as there is no direct sales involved from website.

Target Market(s)

Homeowners in USA and Insurance agent who sells these insurance.

Industry/Entity Type

Insurance

Number of Pages Required

4 page

Font styles to use
Other font styles liked:
• Open to suggestions

Colors

Designer to choose colors to be used in the design.

Requirements
Must have
• Three most important things: Trustworthy, Authentic, Simple
• Please use colors form logo and grays
• We like: www.hollowmere.com
• https://www.quillfenbrook.com/
• We need Agent Look up tool on home page similar to what is shown on example sites.
• Design:
• Home Page - Open to Ideas
• Insurance (Products) Landing Page - Info similar to: https://www.quillfenbrook.com/insurance/
• Agents Page - https://www.quillfenbrook.com/agents/
• Claims Page - Information similar to: https://www.quillfenbrook.com/claims-center/
• Site Navigation:
• Home
• Insurance
• Claims
• Agents
• About Us
• Contact Us
Nice to have
• Elegant, minimal and clean design that reflects trust and authenticity.
Should not have
• Slider or rotating images - prefer flat design. Not over powering design.

```html
<!DOCTYPE html>
<html lang="en">
<head>
<meta charset="utf-8">
<title>Hearthline Insurance Co.</title>
<link rel="stylesheet" href="https://fonts.googleapis.com/css2?family=Montserrat:wght@400;500;600;700&family=Open+Sans:wght@400;600&display=swap">
<style>
:root{
  --red:#d2232a;
  --navy:#1f3a7a;
  --blue:#2d4b93;
  --blue-deep:#213a7c;
  --ink:#2b2b2b;
  --grey:#666;
  --light:#f2f2f2;
  --white:#fff;
  --dark:#161616;
}
*{margin:0;padding:0;box-sizing:border-box}
html,body{width:1200px;height:4128px;overflow:hidden}
body{position:relative;background:var(--white);font-family:"Open Sans",sans-serif;color:var(--ink)}
.abs{position:absolute}
.brand{display:flex;align-items:center;gap:10px;font-family:"Montserrat",sans-serif;font-weight:700;color:var(--navy);text-transform:uppercase;line-height:1.05}
.brand-mark{width:30px;height:30px;background:var(--red);flex:none}

/* header */
.topline{left:0;top:0;width:1200px;height:5px;background:var(--red)}
.site-header{left:0;top:5px;width:1200px;height:72px;background:var(--white)}
.site-header .brand{position:absolute;left:165px;top:14px;font-size:17px}
.main-nav{position:absolute;left:478px;top:27px;display:flex;gap:38px;font-family:"Montserrat",sans-serif;font-size:13px;font-weight:500;color:#333;letter-spacing:.5px}
.main-nav .active{color:var(--navy);font-weight:700;position:relative}
.main-nav .active::after{content:"";position:absolute;left:50%;top:22px;width:7px;height:7px;border:1.5px solid var(--navy);border-radius:50%;transform:translateX(-50%)}

/* hero */
.hero{left:0;top:77px;width:1200px;height:500px;clip-path:polygon(0 0,100% 0,100% 85%,50% 100%,0 85%);background:linear-gradient(90deg,#0c0c0c 0%,#1c1c1c 45%,#2a2a2a 70%,#151515 100%)}
.hero-photo{position:absolute;right:0;top:0;width:640px;height:500px;background:radial-gradient(ellipse at 60% 45%,#4a4a4a 0%,#2a2a2a 45%,transparent 75%)}
.hero-title{position:absolute;left:162px;top:190px;width:430px;font-family:"Montserrat",sans-serif;font-weight:700;font-size:21px;line-height:1.9;color:var(--white)}

/* welcome */
.welcome-title{left:0;top:683px;width:1200px;display:flex;justify-content:center;align-items:center;gap:14px;font-family:"Montserrat",sans-serif;font-weight:700;font-size:32px;color:var(--red)}
.welcome-title .brand{font-size:20px}
.welcome-text{left:186px;top:764px;width:828px;text-align:center;font-size:13px;line-height:1.7;color:#555}
.btn-read{left:515px;top:862px;width:170px;height:36px;display:flex}
.btn-read span{flex:1;background:var(--navy);color:var(--white);font-family:"Montserrat",sans-serif;font-size:13px;font-weight:600;letter-spacing:1px;display:flex;align-items:center;justify-content:center}
.btn-read i{width:50px;background:var(--red);display:flex;align-items:center;justify-content:center}

/* dividers */
.divider{display:flex;align-items:center;justify-content:center;gap:8px;width:1200px;left:0}
.divider b{width:36px;height:1px;background:currentColor;opacity:.6}
.divider em{width:14px;height:16px;background:currentColor}

/* services */
.services{left:0;top:963px;width:1200px;height:1101px;clip-path:polygon(0 90px,50% 0,100% 90px,100% 1040px,50% 100%,0 1040px);background:linear-gradient(180deg,#3553a0 0%,#2d4b93 40%,#22407f 100%)}
.services-photo{position:absolute;inset:0;background:radial-gradient(ellipse at 30% 55%,rgba(255,255,255,.12),transparent 60%),radial-gradient(ellipse at 80% 40%,rgba(255,255,255,.08),transparent 55%)}
.section-title{left:0;width:1200px;text-align:center;font-family:"Montserrat",sans-serif;font-weight:700;font-size:38px;letter-spacing:1px}
.services .section-title{top:120px;color:var(--white)}
.services .divider{top:183px;color:var(--white)}
.services-lead{position:absolute;left:200px;top:228px;width:800px;text-align:center;color:var(--white);font-size:13px;line-height:1.75}
.card{position:absolute;width:276px;height:335px;background:var(--white);clip-path:polygon(0 0,100% 0,100% 92%,50% 100%,0 92%);text-align:center}
.card-photo{height:165px}
.card h3{margin-top:14px;font-family:"Montserrat",sans-serif;font-weight:700;font-size:24px;color:var(--navy);letter-spacing:.5px}
.card p{margin:8px 22px 0;font-size:12.5px;line-height:1.5;color:#444}
.card.featured{background:var(--red)}
.card.featured h3,.card.featured p{color:var(--white)}
.plus{position:absolute;width:34px;height:24px;background:var(--navy);color:var(--white);font:700 20px/24px "Montserrat",sans-serif;text-align:center}
.plus.on-red{background:var(--white);color:var(--red)}

/* availability */
.availability .section-title{top:2178px;font-size:36px}
.availability .divider{top:2245px;color:var(--red)}
.avail-text{left:0;top:2300px;width:1200px;text-align:center;font-family:"Montserrat",sans-serif;font-size:24px;line-height:1.7;color:#222}
.avail-text strong{color:var(--red);font-size:34px;font-weight:500}

/* claims & agents */
.duo{left:0;top:2458px;width:1200px;height:454px;clip-path:polygon(0 0,50% 50px,100% 0,100% 420px,50% 100%,0 420px);background:linear-gradient(180deg,#3553a0,#263f86)}
.duo-col{position:absolute;top:110px;width:420px;text-align:center;color:var(--white)}
.duo-col h2{font-family:"Montserrat",sans-serif;font-weight:700;font-size:28px;letter-spacing:1px}
.duo-col .divider{position:relative;width:100%;margin-top:22px;color:var(--white)}
.duo-col p{margin:26px auto 0;width:360px;font-size:13.5px;line-height:1.65}
.btn-ghost{display:inline-flex;margin-top:20px;height:34px}
.btn-ghost span{background:var(--white);color:#333;font-family:"Montserrat",sans-serif;font-size:12px;font-weight:600;letter-spacing:1px;padding:0 20px;display:flex;align-items:center}
.btn-ghost i{width:44px;background:var(--red);display:flex;align-items:center;justify-content:center}
.duo-link{display:block;margin-top:6px;font-size:12.5px;text-decoration:underline}

/* testimonials */
.testimonials .section-title{top:3022px;font-size:36px}
.testimonials .divider{top:3090px;color:var(--red)}
.testi-art{left:410px;top:3160px;width:380px;height:215px}
.quote-box{left:187px;top:3404px;width:826px;height:152px;border:1px solid #ddd;border-radius:6px;text-align:center;padding:24px 70px 0}
.quote-box p{font-size:13px;line-height:1.75;color:#333}
.quote-box cite{display:block;margin-top:6px;font-style:normal;font-family:"Montserrat",sans-serif;font-weight:700;font-size:13px;color:var(--red)}

/* footer */
.site-footer{left:0;top:3619px;width:1200px;height:509px;clip-path:polygon(0 0,50% 55px,100% 0,100% 100%,0 100%);background:linear-gradient(180deg,#2a2a2a 0%,#1b1b1b 45%,#0f0f0f 100%)}
.footer-city{position:absolute;inset:0;background:linear-gradient(0deg,rgba(190,120,60,.22) 0%,transparent 45%),radial-gradient(ellipse at 50% 100%,rgba(255,170,90,.18),transparent 60%)}
.site-footer .brand{position:absolute;left:440px;top:92px;color:var(--white);font-size:26px;font-weight:600}
.site-footer .brand-mark{width:50px;height:50px;background:#cfcfcf}
.f-head{font-family:"Montserrat",sans-serif;font-weight:700;font-size:14px;color:var(--white);letter-spacing:.5px}
.f-head span{color:var(--red)}
.f-col{position:absolute;top:212px;color:var(--white)}
.f-links{list-style:none;margin-top:24px;font-family:"Montserrat",sans-serif;font-size:12px;line-height:2.55}
.f-links li{padding-left:6px}
.f-contact{margin-top:24px;font-size:12px;line-height:1.5}
.f-row{display:flex;gap:12px;margin-bottom:20px}
.f-row svg{flex:none;margin-top:2px}
.f-row b{font-family:"Montserrat",sans-serif;font-weight:600;font-size:12.5px;display:block}
.f-pair{display:flex;gap:40px}
.f-social{list-style:none;margin-top:24px;font-size:12px}
.f-social li{display:flex;align-items:center;gap:12px;margin-bottom:17px}
.f-social li i{width:24px;height:24px;border-radius:50%;background:var(--red)}
.copyright{position:absolute;left:0;bottom:12px;width:1200px;text-align:center;font-size:11.5px;color:#ddd}
</style>
</head>
<body>

<div class="abs topline"></div>
<header class="abs site-header">
  <div class="brand"><span class="brand-mark"></span><span>Hearthline<br>Insurance Co.</span></div>
  <nav class="main-nav">
    <span class="active">HOME</span><span>INSURANCE</span><span>CLAIMS</span><span>AGENT</span><span>ABOUT US</span><span>CONTACT US</span>
  </nav>
</header>

<section class="abs hero">
  <div class="hero-photo" role="img" aria-label="Businessman in a dark suit cupping his hands protectively around a small white house outline"></div>
  <h1 class="hero-title">We Are Selling Homeowners<br>Insurance Policy / Tenants Policy/<br>Flood Insurance In Usa In Few States<br>And Planning To Expand Nationally.</h1>
</section>

<section class="welcome">
  <h2 class="abs welcome-title">WELCOME TO <span class="brand"><span class="brand-mark"></span><span>Hearthline<br>Insurance Co.</span></span></h2>
  <p class="abs welcome-text">Lorem ipsum dolor sit amet, consectetuer adipiscing elit, sed diam nonummy nibh euismod tincidunt ut laoreet dolore magna aliquam erat volutpat. Ut wisi enim ad minim veniam, quis nostrud exerci tation ullamcorper suscipit lobortis nisl ut aliquip ex ea commodo consequat. Duis autem vel eum iriure dolor in hendrerit in vulputate velit esse molestie consequat.</p>
  <div class="abs btn-read"><span>READ MORE</span><i><svg width="20" height="12" viewBox="0 0 20 12"><path d="M0 6h17M12 1l5 5-5 5" stroke="#fff" stroke-width="2" fill="none"/></svg></i></div>
</section>

<section class="abs services">
  <div class="services-photo" role="img" aria-label="Blue-toned photo of a family jumping on a beach"></div>
  <h2 class="abs section-title">OUR SERVICES</h2>
  <div class="abs divider"><b></b><em></em><b></b></div>
  <p class="services-lead">Hearthline Insurance Company Offers A Wide Range Of Coverage Options And Policies To Fit Your Individual Needs And Budget. Learn More Below To Discover Which Ao Policy Is Right For You.</p>

  <article class="card featured" style="left:162px;top:308px">
    <div class="card-photo" role="img" aria-label="Couple looking at a damaged ceiling at home" style="background:linear-gradient(135deg,#c9b79a,#8a6d52)"></div>
    <h3>HOME</h3>
    <p>Your home is a big asset. With a homeowner's insurance policy from us you can protect your home from the unexpected inside and out.</p>
  </article>
  <div class="plus on-red" style="left:283px;top:618px">+</div>

  <article class="card" style="left:462px;top:308px">
    <div class="card-photo" role="img" aria-label="Condominium building with smoke from a fire" style="background:linear-gradient(135deg,#c9c9c9,#6d6d6d)"></div>
    <h3>CONDO</h3>
    <p>Your association insurance may cover the building, but you need a separate policy to protect your individual unit and personal property.</p>
  </article>
  <div class="plus" style="left:583px;top:618px">+</div>

  <article class="card" style="left:762px;top:308px">
    <div class="card-photo" role="img" aria-label="Group of renters standing on a sunny street" style="background:linear-gradient(135deg,#9fb58a,#5f7a55)"></div>
    <h3>RENTERS</h3>
    <p>Would you have money to replace assets if you were a victim of a fire or theft? Renters insurance can help you feel secure in your rental.</p>
  </article>
  <div class="plus" style="left:883px;top:618px">+</div>

  <article class="card" style="left:162px;top:688px">
    <div class="card-photo" role="img" aria-label="Couple meeting with an insurance advisor at a desk" style="background:linear-gradient(135deg,#d8dde4,#8e9aa8)"></div>
    <h3>SEASONAL</h3>
    <p>There's only so much you can do to protect your secondary property when you aren't around, but an insurance plan can help protect your assets.</p>
  </article>
  <div class="plus" style="left:283px;top:998px">+</div>

  <article class="card" style="left:462px;top:688px">
    <div class="card-photo" role="img" aria-label="House surrounded by flood water" style="background:linear-gradient(180deg,#8e9a76,#5d6b50)"></div>
    <h3>FLOOD</h3>
    <p>You may not be required to purchase flood insurance by law, but the benefits of extra coverage for your home outweigh the risks.</p>
  </article>
  <div class="plus" style="left:583px;top:998px">+</div>

  <article class="card" style="left:762px;top:688px">
    <div class="card-photo" role="img" aria-label="Couple sharing a red umbrella outdoors" style="background:linear-gradient(135deg,#b7c7a2,#c24a4a)"></div>
    <h3>UMBRELLA</h3>
    <p>Personal umbrella insurance helps provide you with extra protection that goes beyond what your homeowners or automobile liability policies cover.</p>
  </article>
  <div class="plus" style="left:883px;top:998px">+</div>
</section>

<section class="availability">
  <h2 class="abs section-title"><span style="color:var(--red)">24/7</span> <span style="color:var(--navy)">AVAILABILITY</span></h2>
  <div class="abs divider"><b></b><em></em><b></b></div>
  <p class="abs avail-text">We are here when you need us the most. Our Emergency Claims Service team<br>is available <strong>24</strong> hours a day, <strong>7</strong> days a week, <strong>365</strong> days a year.</p>
</section>

<section class="abs duo">
  <div class="duo-col" style="left:170px">
    <h2>CLAIMS PROCESS</h2>
    <div class="divider"><b></b><em></em><b></b></div>
    <p>Accidents are stressful, but reporting and viewing your claim shouldn't be. Whether you need to report a claim or check an existing one, Hearthline Insurance Company can help.</p>
    <div class="btn-ghost"><span>GET STARTED</span><i><svg width="20" height="12" viewBox="0 0 20 12"><path d="M0 6h17M12 1l5 5-5 5" stroke="#fff" stroke-width="2" fill="none"/></svg></i></div>
  </div>
  <div class="duo-col" style="left:607px">
    <h2>FOR AGENTS</h2>
    <div class="divider"><b></b><em></em><b></b></div>
    <p>Whether you're a seasoned insurance agent looking to expand your agency or are new to the industry, we're ready to help you help others.</p>
    <div class="btn-ghost"><span>AGENT LOGIN</span><i><svg width="20" height="12" viewBox="0 0 20 12"><path d="M0 6h17M12 1l5 5-5 5" stroke="#fff" stroke-width="2" fill="none"/></svg></i></div>
    <span class="duo-link">Become an Agent</span>
  </div>
</section>

<section class="testimonials">
  <h2 class="abs section-title"><span style="color:var(--red)">CLIENT</span> <span style="color:var(--navy)">TESTIMONIALS</span></h2>
  <div class="abs divider"><b></b><em></em><b></b></div>
  <svg class="abs testi-art" viewBox="0 0 380 215" role="img" aria-label="Diamond-shaped photos of happy client families">
    <polygon points="60,40 120,100 60,160 0,100" fill="#d9dde2"/>
    <polygon points="320,40 380,100 320,160 260,100" fill="#d9dde2"/>
    <polygon points="190,215 160,185 220,185" fill="#333"/>
    <polygon points="190,0 300,100 190,200 80,100" fill="#c7b7a4"/>
  </svg>
  <blockquote class="abs quote-box">
    <p>Lorem ipsum dolor sit amet, consectetuer adipiscing elit, sed diam nonummy nibh euismod tincidunt ut laoreet dolore magna aliquam erat volutpat. Ut wisi enim ad minim veniam, quis nostrud exerci tation ullamcorper suscipit lobortis nisl ut aliquip ex ea commodo consequat.</p>
    <cite>- Lorem Ipsum</cite>
  </blockquote>
</section>

<footer class="abs site-footer">
  <div class="footer-city" role="img" aria-label="City skyline at dusk"></div>
  <div class="brand"><span class="brand-mark"></span><span>Hearthline<br>Insurance Co.</span></div>

  <div class="f-col" style="left:195px">
    <div class="f-head">QUICK <span>LINKS</span></div>
    <ul class="f-links"><li>HOME</li><li>INSURANCE</li><li>CLAIMS</li><li>AGENT</li><li>ABOUT US</li><li>CONTACT US</li></ul>
  </div>

  <div class="f-col" style="left:449px">
    <div class="f-head">CONTACT <span>DETAILS</span></div>
    <div class="f-contact">
      <div class="f-row">
        <svg width="14" height="18" viewBox="0 0 14 18"><path d="M7 0a7 7 0 0 0-7 7c0 5 7 11 7 11s7-6 7-11a7 7 0 0 0-7-7z" fill="#d2232a"/><circle cx="7" cy="7" r="2.5" fill="#fff"/></svg>
        <div><b>HEARTHLINE INSURANCE</b>Lorem Office<br>200 West Lorem Street,<br>Ipsum 221100<br>NY, USA 60606</div>
      </div>
      <div class="f-pair">
        <div class="f-row">
          <svg width="16" height="16" viewBox="0 0 16 16"><path d="M3 1l3 3-2 2c1 2 3 4 5 5l2-2 3 3-2 3C6 15 1 10 1 3z" fill="#d2232a"/></svg>
          <div><b>PHONE</b>123-456-7890</div>
        </div>
        <div class="f-row">
          <svg width="18" height="13" viewBox="0 0 18 13"><rect width="18" height="13" rx="1" fill="#d2232a"/><path d="M1 1l8 6 8-6" stroke="#fff" stroke-width="1.4" fill="none"/></svg>
          <div><b>EMAIL</b>info@hearthline.com</div>
        </div>
      </div>
    </div>
  </div>

  <div class="f-col" style="left:878px">
    <div class="f-head">FOLLOW <span>US ON</span></div>
    <ul class="f-social">
      <li><i></i>Friendbook</li>
      <li><i></i>Chirper</li>
      <li><i></i>Linkwork</li>
      <li><i></i>Circles +</li>
    </ul>
  </div>

  <p class="copyright">Copyright © 2018 Hearthline. All Right Reserved</p>
</footer>

</body>
</html>
```